Flat bootstrap design for existing site

I'm looking for a modern flat design based around an existing logo. This has to be a custom design (no external templates), and implemented into a bootstrap framework.

The logo is attached as 2 versions - choose whichever you want, that flows better with whatever design you choose.

Added screenshots of the existing site (currently using the default bootstrap layouts). Please make your designs around those pages in the screenshots (i.e. the homepage only has the postal code input and the header). The active page has 3 screenshots, because I wanted to illustrate the other states that would be visible (in the table rows).

This is a moving/junk removal website, just for some context.

Here's some example websites (flat designs) that I like, just to give you an idea of what I'm after.

https://www.plimvora.com/
https://dacklow.com/
https://trevanu.com/
https://quobrintal.com/en/

Coding

Coded - Design and coding required

Number of Pages Required

5+ page

Colors

Designer to choose colors to be used in the design.

Requirements
Must have
• It must be a modern/simple flat design, that is built around the existing logo (attached).
• It has to be implemented using bootstrap.

```html
<!DOCTYPE html>
<html lang="en">
<head>
<meta charset="utf-8">
<title>Drovane – Booking Details</title>
<link href="https://fonts.googleapis.com/css2?family=Raleway:wght@400;500;600;700;800&display=swap" rel="stylesheet">
<style>
  :root{
    --brand:#55cdf6;
    --brand-deep:#4cc6f1;
    --brand-text:#3fbdec;
    --ink:#2b2b2b;
    --muted:#555;
    --panel:#f7f7f7;
    --line:#e6e6e6;
    --white:#fff;
    --ok:#74c567;
    --sent:#3b77b4;
    --wait:#7b7b7b;
  }
  *{box-sizing:border-box;margin:0;padding:0}
  html,body{width:1200px;height:1009px;overflow:hidden}
  body{position:relative;background:var(--white);font-family:'Raleway',sans-serif;color:var(--ink)}
  .site-header{position:absolute;left:0;top:0;width:1200px;height:75px;background:linear-gradient(90deg,var(--brand),var(--brand-deep))}
  .brand{position:absolute;left:99px;top:19px;display:flex;align-items:center;gap:10px;color:var(--white);font-weight:800;font-size:30px;letter-spacing:1px}
  .brand-dot{width:22px;height:22px;border-radius:50%;background:var(--white)}
  .main-nav a{position:absolute;top:0;height:75px;line-height:72px;color:var(--white);text-decoration:none;font-size:13.5px;font-weight:500}
  .nav-book{left:580px}
  .nav-how{left:660px}
  .nav-driver{left:777px;width:158px;text-align:center;background:var(--white);color:var(--brand-text)!important}
  .nav-user{left:958px}
  .nav-user svg{margin-left:5px;vertical-align:middle}
  .booking-panel{position:absolute;left:99px;top:99px;width:1003px;height:384px;background:var(--panel);border:1px solid var(--line)}
  .panel-title{position:absolute;left:27px;top:28px;font-size:15.5px;font-weight:600;letter-spacing:.2px}
  .panel-rule{position:absolute;left:27px;top:61px;width:938px;border-top:1px solid var(--line)}
  .field-label{position:absolute;font-size:14.5px;color:var(--muted)}
  .field{position:absolute;height:46px;background:var(--white);border:1px solid var(--line);border-radius:2px;font-size:12.5px;color:#555;line-height:44px;padding-left:20px}
  .field svg{position:absolute;right:16px;top:15px}
  .btn-update{position:absolute;left:29px;top:306px;width:120px;height:46px;background:var(--brand);color:var(--white);border:none;border-radius:2px;font-family:inherit;font-weight:700;font-size:13px;letter-spacing:1.5px}
  .section-rule{position:absolute;left:99px;top:514px;width:1002px;border-top:1px solid var(--line)}
  .section-title{position:absolute;left:98px;top:538px;font-size:15.5px;font-weight:600}
  .notice{position:absolute;left:99px;top:577px;width:1002px;height:46px;background:var(--panel);border:1px solid var(--line);border-radius:2px;font-size:12.5px;color:#555;line-height:44px;padding-left:20px}
  .drivers{position:absolute;left:99px;top:640px;width:1002px}
  .row{position:absolute;left:0;width:1002px;border-bottom:1px solid var(--line);font-size:12.5px;color:#555}
  .row span{position:absolute;top:50%;transform:translateY(-50%)}
  .row .c-dist{left:167px}
  .row .c-time{left:359px}
  .head{top:0;height:47px;font-size:14.5px;font-weight:600;color:var(--ink)}
  .status{left:503px;width:112px;height:26px;border-radius:2px;color:var(--white);font-size:12px;text-align:center;line-height:26px}
  .ok{background:var(--ok)}
  .sent{background:var(--sent)}
  .wait{background:var(--wait)}
  .pay{left:675px;width:120px;height:42px;background:var(--brand);color:var(--white);border-radius:2px;font-weight:600;font-size:13px;text-align:center;line-height:42px}
  .site-footer{position:absolute;left:0;top:962px;width:1200px;height:47px;background:linear-gradient(90deg,var(--brand),var(--brand-deep));color:var(--white);font-size:13px;text-align:center;line-height:47px}
</style>
</head>
<body>
<header class="site-header">
  <div class="brand"><span class="brand-dot"></span>DROVANE</div>
  <nav class="main-nav">
    <a class="nav-book" href="#">BOOK</a>
    <a class="nav-how" href="#">HOW IT WORKS</a>
    <a class="nav-driver" href="#">BECOME A DRIVER</a>
    <a class="nav-user" href="#">mara@hollendry.com<svg width="8" height="5" viewBox="0 0 8 5"><path d="M0 0h8L4 5z" fill="#fff"/></svg></a>
  </nav>
</header>

<section class="booking-panel">
  <h2 class="panel-title">BOOKING DETAILS</h2>
  <div class="panel-rule"></div>
  <div class="field-label" style="left:27px;top:88px">Package Selected :</div>
  <div class="field-label" style="left:503px;top:88px">Pick-up time selected :</div>
  <div class="field" style="left:29px;top:130px;width:469px">Package 1
    <svg width="9" height="14" viewBox="0 0 9 14"><path d="M0 6L4.5 0 9 6zM0 8h9l-4.5 6z" fill="#555"/></svg></div>
  <div class="field" style="left:505px;top:130px;width:469px;padding-left:18px">July 18 at 4:13am
    <svg width="13" height="14" viewBox="0 0 13 14"><rect x=".5" y="2" width="12" height="11.5" fill="none" stroke="#555"/><path d="M.5 5h12M3 0v3M10 0v3M3 7h2M6 7h2M9 7h2M3 9.5h2M6 9.5h2M9 9.5h2" stroke="#555"/></svg></div>
  <div class="field-label" style="left:27px;top:199px">Description</div>
  <div class="field" style="left:29px;top:240px;width:943px">1 large stove</div>
  <button class="btn-update">UPDATE</button>
</section>

<div class="section-rule"></div>
<h2 class="section-title">DRIVERS IN YOUR AREA</h2>
<div class="notice">Please Stay on this page and be patient,While we contact the drivers and find you one ASAP.</div>

<div class="drivers">
  <div class="row head"><span>Name</span><span class="c-dist">Distance (km)</span><span class="c-time">Agreed Pick-up time</span></div>
  <div class="row" style="top:47px;height:62px"><span>Corin Vale</span><span class="c-dist">4.04km away</span><span class="c-time">July 18 at 4:13am</span><span class="status ok">Time Accepted</span><span class="pay">Make Payment</span></div>
  <div class="row" style="top:109px;height:63px"><span>Tobias Marr</span><span class="c-dist">5.7km away</span><span class="c-time">-</span><span class="status sent">Request Sent</span></div>
  <div class="row" style="top:172px;height:61px"><span>Edric Lanner</span><span class="c-dist">11.13km away</span><span class="c-time">-</span><span class="status sent">Request Sent</span></div>
  <div class="row" style="top:233px;height:61px"><span>Vance Holloway</span><span class="c-dist">11.91km away</span><span class="c-time">-</span><span class="status wait">Pending</span></div>
</div>

<footer class="site-footer">© copyright 2017 Drovane.All Rights Reserved</footer>
</body>
</html>
```